Transform Your Giving

I need a tri-fold brochure that will fit in a standard number 10 business envelope. Meadowlark and Allied Services is a charitable nonprofit. The goal of this brochure is to stimulate people into thinking about other ways to make a donation. The design should communicate the essential information on donation options, create a sense of professional integrity, be graphically sharp, easy to read and laid out in a way that doesn't make the material appear crowded.

```html
<!DOCTYPE html>
<html lang="en">
<head>
<meta charset="utf-8">
<title>Transform Your Giving – Meadowlark and Allied Services</title>
<link href="https://fonts.googleapis.com/css2?family=Fira+Sans:ital,wght@0,300;0,400;0,500;0,600;0,700;1,300;1,600;1,700&display=swap" rel="stylesheet">
<style>
:root{
  --navy:#27266e;
  --green:#3fb44a;
  --ink:#25253a;
  --stage:#7b7b7b;
  --paper:#ffffff;
  --muted:#b9bbbf;
}
*{box-sizing:border-box;margin:0;padding:0}
html,body{width:1096px;height:1200px;overflow:hidden;background:var(--stage)}
body{position:relative;font-family:"Fira Sans",sans-serif;color:var(--ink)}
.spread{position:absolute;left:205px;width:687px;height:515px;display:flex;background:var(--paper)}
.spread--outside{top:63px}
.spread--inside{top:621px}
.panel{position:relative;width:229px;height:515px;overflow:hidden}
.panel--navy{background:var(--navy);color:#fff}
.photo{position:absolute;left:0;width:229px}
.curve{position:absolute;left:0;width:229px}
.icon-defs{position:absolute;width:0;height:0}

/* outside left */
.impact{position:absolute;left:18px;top:275px;width:200px}
.impact h2{font-size:11.5px;font-weight:700;color:var(--navy);letter-spacing:.1px}
.impact p{font-size:9.9px;line-height:1.3;margin-top:1px}
.checks{display:grid;grid-template-columns:59px 1fr;row-gap:8px;margin-top:14px;list-style:none;font-size:10px;font-weight:500}
.checks li{display:flex;align-items:center;gap:6px}
.tick{width:8px;height:8px;flex:none}
.wordmark{font-weight:700;letter-spacing:1px;text-align:center}
.wordmark--faint{position:absolute;left:90px;top:468px;width:110px;color:var(--muted)}
.wordmark--faint .wm-name{font-size:22px}
.wm-sub{display:block;font-size:4px;letter-spacing:.3px;font-weight:600;margin-top:1px}

/* outside middle */
.invite{position:absolute;left:14px;top:17px;width:201px;text-align:center;font-size:8.6px;line-height:1.35;font-weight:500}
.quote{position:absolute;left:14px;top:93px;width:201px;text-align:center;font-size:8.6px;line-height:1.35;font-style:italic;font-weight:300}
.will{position:absolute;left:10px;top:224px;width:209px;text-align:center;font-size:8.6px;line-height:1.3}
.will a{color:var(--green);text-decoration:underline}
.wordmark--navy{position:absolute;left:40px;top:282px;width:149px;color:var(--green)}
.wordmark--navy .wm-name{font-size:30px;color:#fff}
.wordmark--navy .wm-sub{color:#fff;font-size:4.6px}
.contact{position:absolute;left:10px;top:339px;width:209px;text-align:center}
.contact h3{font-size:10.5px;font-weight:700;text-decoration:underline}
.contact .lead{color:var(--green);font-size:8.6px;font-weight:500;line-height:1.35;margin-top:3px}
.contact ul{list-style:none;font-size:8px;font-weight:300;line-height:1.3}
.contact li{margin-top:3px}
.dot{display:block;margin:0 auto 2px;width:8px;height:8px;border-radius:50%;background:var(--green)}
.follow{margin-top:5px;font-size:8.8px;font-weight:700;display:flex;justify-content:center;align-items:center;gap:3px}
.follow span.u{text-decoration:underline;margin-right:2px}
.follow i{display:block;width:9px;height:9px;border-radius:50%;background:var(--green)}

/* outside right (cover) */
.cover-title{position:absolute;top:14px;left:0;width:229px;text-align:center}
.cover-title h1{font-size:16.5px;font-weight:600;color:var(--navy);line-height:1.2}
.cover-title h1 span{display:block;color:var(--green);font-weight:700}
.cover-title p{font-size:8.5px;font-weight:600;color:var(--navy);line-height:1.3;margin-top:5px}
.options{position:absolute;left:0;top:290px;width:229px;height:145px}
.opt-label{position:absolute;font-size:10px;font-weight:500;text-align:center;line-height:1.3;transform:translateX(-50%);white-space:nowrap}
.wordmark--cover{position:absolute;left:30px;top:441px;width:169px;color:var(--navy)}
.wordmark--cover .wm-name{font-size:36px}
.wordmark--cover .wm-sub{font-size:5.2px}

/* inside */
.panel--inside{padding:16px 17px 0 18px;background:linear-gradient(90deg,#fff 88%,#ececec)}
.panel--inside:nth-child(2){background:linear-gradient(90deg,#f1f1f1,#fff 10%,#fff 90%,#efefef)}
.panel--inside:nth-child(3){background:linear-gradient(90deg,#efefef,#fff 10%)}
.intro{font-size:8.6px;line-height:1.3;font-weight:500}
.option{margin-top:9px}
.option-head{display:flex;gap:6px;align-items:flex-start}
.badge{width:52px;height:52px;flex:none}
.option-head h3{font-size:9px;font-weight:600;color:var(--navy);line-height:1.3}
.option-head em{display:block;font-size:8.6px;font-weight:600;color:var(--green);line-height:1.3;margin-top:2px}
.body{font-size:8px;line-height:1.35;font-weight:300;margin-top:3px}
.how{font-size:10px;font-weight:600;color:var(--navy);margin-top:8px}
.bullets{list-style:none;margin-top:6px}
.bullets li{display:flex;gap:4px;font-size:7.8px;line-height:1.35;font-weight:300;margin-bottom:5px}
.bullets .tick{margin-top:2px;width:7px;height:7px}
.body--lg{font-size:8.8px;line-height:1.35}
</style>
</head>
<body>

<svg class="icon-defs" aria-hidden="true">
  <defs>
    <symbol id="i-tick" viewBox="0 0 10 10"><circle cx="5" cy="5" r="5" fill="#27266e"/><path d="M2.8 5.1l1.5 1.5 3-3.1" fill="none" stroke="#fff" stroke-width="1.3"/></symbol>
    <symbol id="i-tick-navy" viewBox="0 0 10 10"><circle cx="5" cy="5" r="5" fill="#27266e"/><path d="M2.8 5.1l1.5 1.5 3-3.1" fill="none" stroke="#fff" stroke-width="1.3"/></symbol>
    <symbol id="i-chart" viewBox="0 0 40 40"><g fill="none" stroke="#fff" stroke-width="1.6"><rect x="9" y="24" width="5" height="8"/><rect x="17" y="19" width="5" height="13"/><rect x="25" y="14" width="5" height="18"/><path d="M8 21l9-6 5 3 9-8"/><path d="M27 10h4v4"/><path d="M7 33h26"/></g></symbol>
    <symbol id="i-bank" viewBox="0 0 40 40"><g fill="none" stroke="#fff" stroke-width="1.6"><path d="M8 15l12-7 12 7z"/><path d="M9 15h22M9 31h22M8 34h24"/><path d="M12 18v11M17 18v11M23 18v11M28 18v11"/></g></symbol>
    <symbol id="i-gift" viewBox="0 0 40 40"><g fill="none" stroke="#fff" stroke-width="1.6"><rect x="9" y="16" width="22" height="6"/><rect x="11" y="22" width="18" height="11"/><path d="M20 16v17"/><path d="M20 16c-3-5-8-6-8-3s5 3 8 3c3 0 8 0 8-3s-5-2-8 3"/></g></symbol>
    <symbol id="i-coin" viewBox="0 0 40 40"><g fill="none" stroke="#fff" stroke-width="1.6"><circle cx="20" cy="20" r="11"/><circle cx="20" cy="20" r="7"/><path d="M20 15v10"/></g></symbol>
    <symbol id="i-plan" viewBox="0 0 40 40"><g fill="none" stroke="#fff" stroke-width="1.4"><rect x="9" y="11" width="22" height="21" rx="2"/><path d="M9 17h22"/><circle cx="20" cy="11" r="4" fill="#27266e"/><path d="M20 9v4"/><path d="M13 21h3M18 21h3M24 21h3M13 25h3M18 25h3M24 25h3M13 29h3M24 29h3"/></g></symbol>
  </defs>
</svg>

<!-- Outside spread -->
<section class="spread spread--outside">

  <article class="panel panel--impact">
    <div class="photo" style="top:0;height:270px;background:linear-gradient(160deg,#d9cbb8,#a88f72 55%,#8f7a66)" role="img" aria-label="Photo of a smiling older couple embracing at home"></div>
    <svg class="curve" style="top:238px;height:40px" viewBox="0 0 229 40" preserveAspectRatio="none"><path d="M0 30 Q114 -8 229 30 V40 H0z" fill="#fff"/><path d="M0 30 Q114 -8 229 30" fill="none" stroke="#3fb44a" stroke-width="4"/></svg>
    <div class="impact">
      <h2>THE IMPACT OF YOUR GIFT</h2>
      <p>Your generosity drives our mission. With every Smart gift you’re supporting Meadowlark and Allied Services. Join our community of Smart Givers today and make an enduring impact. With Smart Giving your generosity reaches further. Begin your Smart Giving journey with us today.</p>
      <ul class="checks">
        <li><svg class="tick"><use href="#i-tick"/></svg>DAFs</li>
        <li><svg class="tick"><use href="#i-tick"/></svg>Stocks and Securities</li>
        <li><svg class="tick"><use href="#i-tick"/></svg>QCDs</li>
        <li><svg class="tick"><use href="#i-tick"/></svg>Charitable Annuity</li>
        <li><svg class="tick"><use href="#i-tick"/></svg>Crypto</li>
      </ul>
    </div>
    <div class="wordmark wordmark--faint"><span class="wm-name">MAS</span><span class="wm-sub">MEADOWLARK AND ALLIED SERVICES, INC.</span></div>
  </article>

  <article class="panel panel--navy">
    <p class="invite">To learn more about Smart Giving Options and how they can benefit you and Meadowlark and Allied Services, please reach out to our team. We’re here to help you navigate these giving methods and answer any question you may have.</p>
    <div class="photo" style="top:95px;height:140px;background:linear-gradient(200deg,rgba(39,38,110,0) 20%,#33327e 55%,rgba(39,38,110,0) 90%)" role="img" aria-label="Faint photo of two reaching hands"></div>
    <p class="quote">Being kind to others is a way of<br>being good to yourself.<br>Miriam Castell</p>
    <p class="will">If you do not have a will, go to<br><a>www.SimpleWillNow.org</a><br>In 20 minutes you can have a legal will – for free.</p>
    <div class="wordmark wordmark--navy"><span class="wm-name">MAS</span><span class="wm-sub">MEADOWLARK AND ALLIED SERVICES, INC.</span></div>
    <div class="contact">
      <h3>CONTACT US</h3>
      <p class="lead">Have more question? Please contact us at Meadowlark and Allied Services</p>
      <ul>
        <li><span class="dot"></span>1420 Prairie View Ave.<br>Suite 6 Larkfield, ND 58190</li>
        <li><span class="dot"></span>555-014-2200 (ext. 100)</li>
        <li><span class="dot"></span>lharmon@meadowlarkallied.org</li>
        <li><span class="dot"></span>www.meadowlarkallied.org</li>
      </ul>
      <p class="follow"><span class="u">FOLLOW US:</span><i></i><i></i></p>
    </div>
  </article>

  <article class="panel panel--cover">
    <div class="cover-title">
      <h1>Transform Your Giving<span>Be Strategic, Be Smart</span></h1>
      <p>Discover the impact of Smart Giving with<br>Meadowlark and Allied Services</p>
    </div>
    <div class="photo" style="top:90px;height:205px;background:linear-gradient(120deg,#9fb8b8,#e8ddc8 50%,#f3d48a)" role="img" aria-label="Photo of a laughing older couple outdoors in sunlight"></div>
    <svg class="curve" style="top:86px;height:30px" viewBox="0 0 229 30" preserveAspectRatio="none"><path d="M0 0 H229 V28 Q114 -8 0 28z" fill="#fff"/><path d="M0 28 Q114 -8 229 28" fill="none" stroke="#3fb44a" stroke-width="3.5"/></svg>
    <svg class="curve" style="top:262px;height:40px" viewBox="0 0 229 40" preserveAspectRatio="none"><path d="M0 30 Q114 -8 229 30 V40 H0z" fill="#fff"/><path d="M0 30 Q114 -8 229 30" fill="none" stroke="#3fb44a" stroke-width="4"/></svg>
    <div class="options">
      <svg width="229" height="145" viewBox="0 0 229 145">
        <g stroke="#27266e" stroke-width="1.2" stroke-dasharray="1.5 1.5"><path d="M66 23h31M140 23h31M97 83h31"/></g>
        <g fill="#27266e" stroke="#fff" stroke-width="1.5">
          <circle cx="45" cy="23" r="20"/><circle cx="116" cy="23" r="20"/><circle cx="184" cy="23" r="20"/>
          <circle cx="78" cy="83" r="20"/><circle cx="151" cy="83" r="20"/>
        </g>
        <g fill="none" stroke="#27266e" stroke-width="1"><circle cx="45" cy="23" r="21.5"/><circle cx="116" cy="23" r="21.5"/><circle cx="184" cy="23" r="21.5"/><circle cx="78" cy="83" r="21.5"/><circle cx="151" cy="83" r="21.5"/></g>
        <use href="#i-coin" x="29" y="7" width="32" height="32"/>
        <use href="#i-bank" x="100" y="7" width="32" height="32"/>
        <use href="#i-gift" x="168" y="7" width="32" height="32"/>
        <use href="#i-chart" x="62" y="67" width="32" height="32"/>
        <use href="#i-plan" x="135" y="67" width="32" height="32"/>
      </svg>
      <span class="opt-label" style="left:45px;top:48px">CRYPTO</span>
      <span class="opt-label" style="left:116px;top:48px">DAF’S</span>
      <span class="opt-label" style="left:184px;top:48px">QCDS</span>
      <span class="opt-label" style="left:78px;top:108px">STOCKS &amp;<br>SECURITIES</span>
      <span class="opt-label" style="left:151px;top:108px">CHARITABLE<br>ANNUITY</span>
    </div>
    <div class="wordmark wordmark--cover"><span class="wm-name">MAS</span><span class="wm-sub">MEADOWLARK AND ALLIED SERVICES, INC.</span></div>
  </article>
</section>

<!-- Inside spread -->
<section class="spread spread--inside">

  <article class="panel panel--inside">
    <p class="intro">We would like to introduce you to five Strategic and Smart ways to give that could potentially be more beneficial to you compared to traditional cash donations. We encourage you to keep this information as a guide for your future contributions.</p>
    <div class="option">
      <div class="option-head">
        <svg class="badge" viewBox="0 0 52 52"><circle cx="26" cy="26" r="24.5" fill="#fff" stroke="#3fb44a" stroke-width="2.5"/><circle cx="26" cy="26" r="20" fill="#27266e"/><use href="#i-chart" x="10" y="10" width="32" height="32"/></svg>
        <h3>Gifts of Stocks or Appreciated Assets Strategic &amp; Smart<em>Consider your long-term publicly traded stock as a way to give to your favorite charity.</em></h3>
      </div>
      <p class="body">You can make a significantly bigger impact when you donate long-term appreciated securities, including stock, mutual funds, &amp; bonds, directly to your favorite charity.</p>
      <p class="how">How Does It Work?</p>
      <p class="body" style="margin-top:1px">When you donate stock to a charity, you will generally take a tax deduction for the full market value. Because you are donating stock, your contribution &amp; tax deduction may be significantly higher than contributing the after-tax proceeds. The same benefits apply when you donate mutual funds or bonds.</p>
    </div>
    <div class="option" style="margin-top:12px">
      <div class="option-head">
        <svg class="badge" viewBox="0 0 52 52"><circle cx="26" cy="26" r="24.5" fill="#fff" stroke="#3fb44a" stroke-width="2.5"/><circle cx="26" cy="26" r="20" fill="#27266e"/><use href="#i-bank" x="10" y="10" width="32" height="32"/></svg>
        <h3>Donor-Advised Fund (DAF)<br>Strategic &amp; Smart<em>Consider a DAF – a simple, flexible, and tax-advantageous way to give to your favorite charities.</em></h3>
      </div>
      <p class="body">A Donor-Advised Fund (DAF), is like a charitable investment account for the sole purpose of supporting your favorite charities.</p>
      <p class="how">How Does It Work?</p>
      <p class="body" style="margin-top:1px;font-size:7.6px">You establish a DAF &amp; contribute cash, stocks, or non-publicly traded assets, cryptocurrency, &amp; private company stock to be eligible for an immediate tax deduction. Those funds are contributed for tax-free growth. You can recommend grants be made from your DAF to any IRS qualified public charity.</p>
    </div>
  </article>

  <article class="panel panel--inside">
    <div class="option" style="margin-top:0">
      <div class="option-head">
        <svg class="badge" viewBox="0 0 52 52"><circle cx="26" cy="26" r="24.5" fill="#fff" stroke="#3fb44a" stroke-width="2.5"/><circle cx="26" cy="26" r="20" fill="#27266e"/><use href="#i-gift" x="10" y="10" width="32" height="32"/></svg>
        <h3 style="font-size:8.6px">Qualified Charitable Distributions (QCDs) Strategic &amp; Smart<em style="font-size:8.2px">Consider a QCD – when planning your IRA withdrawal strategy… &amp; donate to your favorite charity.</em></h3>
      </div>
      <p class="body">IRA owners at age 70 ½ or over can transfer dollars from their IRA to charity tax-free each year. These transfers known as Qualified Charitable Distributions (QCDs) offer eligible older Americans a great way to easily give to charity.</p>
      <p class="how">How Does It Work?</p>
      <p class="body" style="margin-top:1px">Are you 72 and required to take a minimum distribution (RMD) from your IRA but do not need the funds? Consider a Qualified Charitable Distribution. Normally, distributions from a traditional IRA are taxable when received. With a QCD, these distributions become tax-free when paid directly from the IRA to your favorite eligible charity. An IRA owner wishing to make a QCD should contact their IRA trustee, allowing time to complete the transaction before the end of the year to receive the tax benefit.</p>
    </div>
    <div class="option" style="margin-top:16px">
      <div class="option-head">
        <svg class="badge" viewBox="0 0 52 52"><circle cx="26" cy="26" r="24.5" fill="#fff" stroke="#3fb44a" stroke-width="2.5"/><circle cx="26" cy="26" r="20" fill="#27266e"/><use href="#i-plan" x="10" y="10" width="32" height="32"/></svg>
        <h3 style="font-size:8.6px">Charitable Gift Annuity<br>Strategic &amp; Smart<em style="font-size:8.2px">Consider establishing a Charitable Gift Annuity</em></h3>
      </div>
      <p class="body">You make a donation to a single charity. The gift is set aside in a reserve account and invested.</p>
      <p class="how">How Does It Work?</p>
      <p class="body" style="margin-top:1px">A charitable gift annuity is a contract between a donor &amp; a charity. As a donor, you make a sizable gift to charity using cash, securities, or possibly other assets. This money is then invested. In return, you become eligible to take a partial tax deduction for your donation, plus you receive a fixed stream of income from the charity for the rest of your life. At the end of your life (as well as your spouse’s, if you’re giving as a couple), the charity receives the remainder of the gift.</p>
    </div>
  </article>

  <article class="panel panel--inside">
    <div class="option" style="margin-top:0">
      <div class="option-head">
        <svg class="badge" viewBox="0 0 52 52"><circle cx="26" cy="26" r="24.5" fill="#fff" stroke="#3fb44a" stroke-width="2.5"/><circle cx="26" cy="26" r="20" fill="#27266e"/><use href="#i-coin" x="10" y="10" width="32" height="32"/></svg>
        <h3 style="font-size:10px">Cryptocurrency<br>Strategic &amp; Smart<em>Consider donating Bitcoin and other cryptocurrencies to your favorite charity.</em></h3>
      </div>
      <p class="body body--lg">Bitcoin and other cryptocurrencies can be donated to charity just like other appreciated assets such as stocks and other business interests. Before you sell bitcoin &amp; donate the after-tax proceeds, consider donating your bitcoin directly to a favorite charity.</p>
      <p class="how">How Does It Work?</p>
      <p class="body" style="margin-top:1px">Many donors find it useful to open a Donor-Advised Fund (DAF). This strategy includes two significant benefits, both for you and your favorite charity.</p>
      <ul class="bullets">
        <li><svg class="tick"><use href="#i-tick-navy"/></svg><span>Your tax deduction will be equal to the fair market value of the donated bitcoin (as determined by a qualified appraisal).</span></li>
        <li><svg class="tick"><use href="#i-tick-navy"/></svg><span>Your cryptocurrency donation is tax-smart because it may eliminate capital gains taxes on the value / appreciation AND your favorite charity will receive 100% of the value of the contribution.</span></li>
      </ul>
      <p class="body">Often charities are not able to accept direct donations of bitcoin/crypto so using a DAF is a great way to donate these assets.</p>
    </div>
    <div class="photo" style="top:378px;height:137px;background:linear-gradient(150deg,#5f7f86,#b9a58f 55%,#7d6a5c)" role="img" aria-label="Photo of a smiling older couple sitting together on a sofa"></div>
    <svg class="curve" style="top:366px;height:30px" viewBox="0 0 229 30" preserveAspectRatio="none"><path d="M0 0 H229 V28 Q114 -8 0 28z" fill="#fff"/><path d="M0 28 Q114 -8 229 28" fill="none" stroke="#3fb44a" stroke-width="3.5"/></svg>
  </article>
</section>

</body>
</html>
```